Redesign of an existing homepage

This site needs a redesign
https://www.wanderhof-kelbach.de
This page with the accommodation options is important for the customer
https://www.wanderhof-kelbach.de/gastgeber/
Till now there is a new logo. See attachment. That's all I have.
It would make sense to use the colors of the logo in the redesign.
footer.jpg.
I would put this info into the footer. The graphic (Infomaterial) is not needed.
a new menu - links.jpg
This info can be put in a new menu. Therefore the right column is gone and there is more space for the design.
NEW:
Please keep in mind that the Icons are important and shall be displayed under every accommodation

```html
<!DOCTYPE html>
<html lang="de">
<head>
<meta charset="utf-8">
<title>Wanderhof Kelbach – Urlaub im Kelbachtal</title>
<link href="https://fonts.googleapis.com/css2?family=Barlow:wght@400;500;600;700&family=Lexend:wght@700;800;900&display=swap" rel="stylesheet">
<style>
:root{
  --blue:#1d6fb8;
  --blue-dark:#15599a;
  --green:#7ab51d;
  --ink:#222;
  --text:#333;
  --muted:#666;
  --black:#0b0b0b;
  --bar:#2a2a2a;
  --white:#fff;
}
*{margin:0;padding:0;box-sizing:border-box}
html,body{width:1200px;height:4030px;overflow:hidden}
body{position:relative;font-family:"Barlow",sans-serif;color:var(--text);background:var(--white)}
.abs{position:absolute}
a{color:inherit;text-decoration:none}

/* top bar */
.topbar{position:absolute;left:0;top:0;width:1200px;height:35px;background:var(--blue);color:var(--white);font-size:12.5px;font-weight:500}
.topbar .group{position:absolute;top:0;height:35px;display:flex;align-items:center;gap:16px;white-space:nowrap}
.topbar .group.left{left:141px}
.topbar .group.right{right:141px;gap:12px}
.topbar .item{display:flex;align-items:center;gap:5px}
.topbar svg{width:14px;height:14px;flex:none}

/* nav */
.nav{position:absolute;left:0;top:35px;width:1200px;height:50px;background:var(--white);font-size:13.5px;color:var(--ink)}
.nav .group{position:absolute;top:0;height:50px;display:flex;align-items:center;white-space:nowrap}
.nav .group.left{left:141px;gap:40px}
.nav .group.right{right:141px;gap:44px}
.nav a.active{color:var(--green)}
.brand-badge{position:absolute;left:524px;top:0;width:157px;height:113px;background:var(--white);border-radius:0 0 26px 26px;display:flex;flex-direction:column;align-items:center;justify-content:center;gap:6px;z-index:3}
.brand-badge .dot{width:44px;height:44px;border-radius:50%;background:var(--blue)}
.brand-name{font-family:"Barlow",sans-serif;font-weight:700;color:var(--blue);font-size:14px;text-align:center;line-height:1.1;letter-spacing:.3px}

/* hero */
.hero{position:absolute;left:0;top:85px;width:1200px;height:590px;overflow:hidden}
.hero-photo{position:absolute;inset:0;background:linear-gradient(180deg,#cfd9e2 0%,#aebfcf 25%,#7f98ad 45%,#3f6785 70%,#1f4a6b 100%)}
.hero-word{position:absolute;left:365px;top:150px;font-family:"Lexend",sans-serif;font-weight:900;font-size:128px;letter-spacing:0;color:rgba(240,245,250,.92);line-height:1;white-space:nowrap}
.hero h1{position:absolute;left:543px;top:322px;font-family:"Lexend",sans-serif;font-weight:800;font-size:37px;line-height:1.05;color:var(--white);white-space:nowrap}
.btn{display:inline-flex;align-items:center;justify-content:center;background:var(--green);color:var(--white);font-weight:500;font-size:13px;border-radius:18px}
.hero .btn{position:absolute;left:544px;top:428px;width:106px;height:35px}
.hero-curve{position:absolute;left:0;top:480px}

/* section heads */
.orn{position:absolute;left:552px;width:96px;height:30px}
.sec-title{position:absolute;left:0;width:1200px;text-align:center;font-weight:600;font-size:33px;color:var(--ink)}
.sec-title .b{color:var(--blue)}

/* welcome */
.fog{position:absolute;left:0;top:900px;width:1200px;height:560px;background:linear-gradient(180deg,rgba(255,255,255,0) 0%,#dfe6ec 30%,#d4dde5 60%,rgba(255,255,255,0) 100%)}
.fog-word{position:absolute;left:180px;top:940px;font-family:"Lexend",sans-serif;font-weight:900;font-size:250px;color:rgba(255,255,255,.6);line-height:1;letter-spacing:6px}
.welcome-text{position:absolute;left:270px;top:884px;width:660px;text-align:center;font-size:12px;line-height:23px;color:var(--ink)}
.people{position:absolute;left:931px;top:868px;width:250px;height:392px;background:radial-gradient(ellipse at 50% 40%,#6f8fb0 0%,#c9b9a6 45%,rgba(220,228,234,0) 72%)}

/* video */
.video{position:absolute;left:266px;top:1258px;width:668px;height:350px;border-radius:12px;background:#9aa0a5;padding:7px}
.video-photo{position:relative;width:100%;height:100%;border-radius:8px;overflow:hidden;background:linear-gradient(180deg,#3c4555 0%,#5c6a78 35%,#3e5a4e 60%,#1e3832 100%)}
.player{position:absolute;left:30px;right:30px;bottom:16px;color:var(--white);font-size:12px}
.player .track{height:3px;background:rgba(255,255,255,.4);border-radius:2px;margin-bottom:10px}
.player .track i{display:block;width:8%;height:3px;background:#e02424}
.player .row{display:flex;align-items:center;gap:12px}

/* cards */
.card{position:absolute;top:1862px;width:212px}
.card .photo{height:317px;border-radius:10px}
.card .info{position:absolute;left:26px;top:242px;width:160px;height:118px;background:var(--white);border-radius:6px;box-shadow:0 6px 16px rgba(0,0,0,.12);text-align:center;padding-top:12px}
.card h3{font-weight:500;font-size:16px;color:var(--ink)}
.card p{font-size:12px;line-height:19px;margin-top:3px;color:var(--ink)}
.more{color:var(--green);font-size:12.5px;font-weight:500;display:inline-flex;align-items:center;gap:4px}
.card .more{position:absolute;left:0;right:0;bottom:12px;justify-content:center}

/* events */
.ev-big{position:absolute;left:141px;top:2514px;width:405px;height:268px;border-radius:8px;background:radial-gradient(circle at 30% 20%,#f29a4a 0%,#b24a2a 30%,#3c2e3c 70%,#1e2030 100%)}
.ev-small{position:absolute;width:237px;height:183px;border-radius:8px;overflow:hidden}
.ev-small span{position:absolute;left:14px;right:14px;bottom:12px;color:var(--white);font-size:14.5px;line-height:23px}
.ev-title{position:absolute;left:141px;top:2809px;font-size:15px;font-weight:500;color:var(--ink)}
.ev-text{position:absolute;left:141px;top:2836px;width:400px;font-size:12.5px;line-height:19px;color:var(--ink)}

/* map & footer */
.map{position:absolute;left:0;top:3210px;width:1200px;height:440px;background:linear-gradient(135deg,#d9efd9 0%,#c9ead2 40%,#d7eede 70%,#cfe8cf 100%)}
.footer-shape{position:absolute;left:0;top:3520px}
.footer{position:absolute;left:0;top:3640px;width:1200px;height:342px;color:var(--white)}
.f-brand{position:absolute;left:128px;top:60px;width:220px;text-align:center}
.f-brand .dot{width:70px;height:70px;border-radius:50%;background:var(--blue);margin:0 auto 10px}
.f-brand .brand-name{font-size:18px}
.hours{position:absolute;left:128px;top:208px;width:220px;text-align:center;font-size:14px;line-height:20px}
.hours h4{font-weight:500;font-size:16px;margin-bottom:14px}
.vline{position:absolute;top:60px;width:1px;height:205px;background:#444}
.f-head{position:absolute;top:64px;font-size:15px;font-weight:500}
.f-links{position:absolute;top:102px;list-style:none;font-size:12.5px;line-height:31.7px}
.f-links li.active{color:var(--green)}
.contact{position:absolute;left:845px;top:100px;font-size:12.5px;line-height:19px}
.contact .row{display:flex;gap:16px;margin-bottom:15px}
.contact svg{width:30px;height:30px;flex:none}
.copy{position:absolute;left:0;top:3982px;width:1200px;height:48px;background:var(--bar);color:#ddd;font-size:12px;text-align:center;line-height:48px}
</style>
</head>
<body>

<header class="topbar">
  <div class="group left">
    <div class="item">
      <svg viewBox="0 0 24 24" fill="none" stroke="#fff" stroke-width="2"><path d="M5 3h4l2 5-3 2a11 11 0 0 0 6 6l2-3 5 2v4a2 2 0 0 1-2 2A17 17 0 0 1 3 5a2 2 0 0 1 2-2z"/></svg>
      01234 / 567 890
    </div>
    <div class="item">
      <svg viewBox="0 0 24 24" fill="#fff"><path d="M2 5h20v14H2z"/><path d="M2 5l10 8 10-8" stroke="#1d6fb8" stroke-width="2" fill="none"/></svg>
      info@wanderhof-kelbach.de
    </div>
  </div>
  <div class="group right">
    <div class="item">
      <svg viewBox="0 0 24 24" fill="none" stroke="#fff" stroke-width="2"><circle cx="12" cy="12" r="9"/><path d="M3 12h18M12 3c3 3 3 15 0 18M12 3c-3 3-3 15 0 18"/></svg>Kelbach
    </div>
    <div class="item">
      <svg viewBox="0 0 24 24" fill="none" stroke="#fff" stroke-width="2"><circle cx="12" cy="12" r="9"/><path d="M3 12h18M12 3c3 3 3 15 0 18M12 3c-3 3-3 15 0 18"/></svg>Kelbach-Land
    </div>
    <div class="item">
      <svg viewBox="0 0 24 24" fill="none" stroke="#fff" stroke-width="2"><circle cx="12" cy="12" r="9"/><path d="M3 12h18M12 3c3 3 3 15 0 18M12 3c-3 3-3 15 0 18"/></svg>Thermenland-Süd
    </div>
  </div>
</header>

<nav class="nav">
  <div class="group left">
    <a class="active" href="https://www.wanderhof-kelbach.de/gastgeber/">Gastgeber</a>
    <a>Kelbachtal</a>
    <a>Freizeit</a>
    <a>Ausflugsziele</a>
  </div>
  <div class="group right">
    <a>Kunst und Kultur</a>
    <a>Veranstaltungen</a>
    <a>Kontakt</a>
  </div>
</nav>
<div class="brand-badge">
  <span class="dot"></span>
  <span class="brand-name">WANDERHOF<br>KELBACH</span>
</div>

<section class="hero">
  <div class="hero-photo" role="img" aria-label="Winterlicher See mit weißer Kirche, Holzboot, verschneiten Bergen und Herbstbäumen"></div>
  <div class="hero-word">BAYERNS</div>
  <h1>Urlaub im Kelbachtal – dem<br>schönsten Fleck Bayerns</h1>
  <a class="btn">Kontakt</a>
  <svg class="hero-curve" width="1200" height="110" viewBox="0 0 1200 110">
    <path d="M0 100 Q420 130 1200 0 L1200 110 L0 110Z" fill="#fff"/>
    <path d="M0 93 Q420 125 1200 -4" fill="none" stroke="#2c5f86" stroke-width="6" opacity=".7"/>
  </svg>
</section>

<!-- welcome -->
<svg class="orn" style="top:752px" viewBox="0 0 96 30"><line x1="0" y1="15" x2="34" y2="15" stroke="#7ab51d" stroke-width="1.5"/><line x1="62" y1="15" x2="96" y2="15" stroke="#1d6fb8" stroke-width="1.5"/><circle cx="48" cy="15" r="12" fill="#1d6fb8"/></svg>
<h2 class="sec-title" style="top:788px;line-height:39px"><span class="b">Willkommen im Kelbachtal und</span><br>im schönsten Fleckchen Bayerns</h2>
<div class="fog"></div>
<div class="fog-word">KELBA</div>
<div class="people" role="img" aria-label="Paar mit Sonnenhut und Landkarte auf Entdeckungstour"></div>
<p class="welcome-text">
Lieber Besucherinnen und Besucher,<br>
Kelbach und Umgebung haben all das, was das Leben lebenswert macht:<br>
Kultur und Natur, Lebensfreude und Genuss, freundliche und aufgeschlossene Menschen...<br>
Ob Kirchen, Brunnen oder andere Baudenkmäler – bei einem Rundgang durch die Kelbacher Hof-Stadt kann man viele liebevolle Details für sich entdecken.<br>
Für Bewegungsfreudige und Erholungssuchende gibt es "Natur pur" in und um Kelbach! Hier kann man sportlich unterwegs sein beim Radeln, Walken, Wandern, Golfen, Reiten und Baden oder einfach nur die Ruhe genießen.<br>
Freizeit und Erholung für die ganze Familie – planen Sie einen Urlaub auf dem Bauernhof, in einer Ferienwohnung oder im Hotel. Ihr Urlaub im Kelbachtal wird ein einmaliges Erlebnis!<br>
Genießen Sie unsere Gastfreundschaft – ein Besuch lohnt sich zu jeder Jahreszeit.<br>
Wir freuen uns auf Sie!<br>
Ihr<br>
Gästeverein Kelbach und Umgebung e. V.
</p>

<div class="video">
  <div class="video-photo" role="img" aria-label="Videovorschau: Bergsee mit Dorf und Spiegelung in der Abenddämmerung">
    <div class="player">
      <div class="track"><i></i></div>
      <div class="row">
        <svg width="12" height="12" viewBox="0 0 12 12" fill="#fff"><rect x="1" y="1" width="3" height="10"/><rect x="7" y="1" width="3" height="10"/></svg>
        <svg width="16" height="14" viewBox="0 0 16 14" fill="#fff"><path d="M1 5h3l4-4v12l-4-4H1z"/><path d="M11 4q2 3 0 6M13 2q4 5 0 10" stroke="#fff" fill="none" stroke-width="1.4"/></svg>
        <span>0:05 / 0:30</span>
        <span style="flex:1"></span>
        <svg width="16" height="16" viewBox="0 0 16 16" fill="none" stroke="#fff" stroke-width="2"><path d="M1 5V1h4M11 1h4v4M15 11v4h-4M5 15H1v-4"/></svg>
      </div>
    </div>
  </div>
</div>

<!-- Freizeit -->
<svg class="orn" style="top:1733px" viewBox="0 0 96 30"><line x1="0" y1="15" x2="34" y2="15" stroke="#7ab51d" stroke-width="1.5"/><line x1="62" y1="15" x2="96" y2="15" stroke="#1d6fb8" stroke-width="1.5"/><circle cx="48" cy="15" r="12" fill="#1d6fb8"/></svg>
<h2 class="sec-title" style="top:1770px"><span class="b">Unsere</span> Freizeit</h2>
<p class="abs" style="left:0;top:1818px;width:1200px;text-align:center;font-size:14px;color:var(--ink)">Freizeit und Erholung für die ganze Familie</p>

<article class="card" style="left:141px">
  <div class="photo" role="img" aria-label="Enten auf einem ruhigen See mit Bäumen" style="background:linear-gradient(180deg,#6f7a52 0%,#c9cbb8 40%,#dfe0d6 100%)"></div>
  <div class="info"><h3>Angeln</h3><p>Angeln am<br>Kelbachsee</p><a class="more">Mehr lesen <svg width="11" height="9" viewBox="0 0 11 9" fill="none" stroke="#7ab51d" stroke-width="1.6"><path d="M0 4.5h9M6 1l3.5 3.5L6 8"/></svg></a></div>
</article>
<article class="card" style="left:377px">
  <div class="photo" role="img" aria-label="Heißluftballon über einem Bergsee" style="background:linear-gradient(180deg,#9fc4dd 0%,#d9765a 35%,#8fb1c8 60%,#5a86a6 100%)"></div>
  <div class="info"><h3>Ballonfahrten</h3><p>Entdecken Sie das<br>Kelbachtal von oben</p><a class="more">Mehr lesen <svg width="11" height="9" viewBox="0 0 11 9" fill="none" stroke="#7ab51d" stroke-width="1.6"><path d="M0 4.5h9M6 1l3.5 3.5L6 8"/></svg></a></div>
</article>
<article class="card" style="left:612px">
  <div class="photo" role="img" aria-label="Frau an einem Marktstand mit regionalen Produkten" style="background:linear-gradient(180deg,#e8a860 0%,#a3583a 45%,#4a2f2a 100%)"></div>
  <div class="info"><h3>Direktvermarkter</h3><p>Günstig direkt beim<br>Hersteller einkaufen</p><a class="more">Mehr lesen <svg width="11" height="9" viewBox="0 0 11 9" fill="none" stroke="#7ab51d" stroke-width="1.6"><path d="M0 4.5h9M6 1l3.5 3.5L6 8"/></svg></a></div>
</article>
<article class="card" style="left:846px">
  <div class="photo" role="img" aria-label="Gruppe junger Leute am Pool" style="background:linear-gradient(180deg,#5b7a5a 0%,#b08270 40%,#2fa9d6 70%,#1d8fc6 100%)"></div>
  <div class="info"><h3>Freibäder</h3><p>Badeseen, Freibäder<br>und Hallenbäder</p><a class="more">Mehr lesen <svg width="11" height="9" viewBox="0 0 11 9" fill="none" stroke="#7ab51d" stroke-width="1.6"><path d="M0 4.5h9M6 1l3.5 3.5L6 8"/></svg></a></div>
</article>
<a class="btn abs" style="left:526px;top:2262px;width:148px;height:33px;font-size:12px">Alle anzeigen Freizeit</a>

<!-- Veranstaltung -->
<svg class="orn" style="top:2404px" viewBox="0 0 96 30"><line x1="0" y1="15" x2="34" y2="15" stroke="#7ab51d" stroke-width="1.5"/><line x1="62" y1="15" x2="96" y2="15" stroke="#1d6fb8" stroke-width="1.5"/><circle cx="48" cy="15" r="12" fill="#1d6fb8"/></svg>
<h2 class="sec-title" style="top:2441px"><span class="b">Unsere</span> Veranstaltung</h2>

<div class="ev-big" role="img" aria-label="Abendliches Fest mit Lichterketten und Menschenmenge"></div>
<h3 class="ev-title">Duis autem vel eum iriuren dolor in hendrerit.</h3>
<p class="ev-text">Lorem ipsum dolor sit amet, cons e ctetuer adipiscing elit. Ullaml corper suscipit lobortis nisl ut aliquip ex ea commodo...</p>
<a class="more abs" style="left:141px;top:2885px">Mehr lesen <svg width="11" height="9" viewBox="0 0 11 9" fill="none" stroke="#7ab51d" stroke-width="1.6"><path d="M0 4.5h9M6 1l3.5 3.5L6 8"/></svg></a>

<div class="ev-small" style="left:566px;top:2514px;background:linear-gradient(180deg,#4f6a3a 0%,#3e4f33 50%,#2a3326 100%)" role="img" aria-label="Radfahrer im Wald"><span>Duis autem vel eum iriuren ok dolor in hendrerit.</span></div>
<div class="ev-small" style="left:823px;top:2514px;background:linear-gradient(180deg,#8a8a88 0%,#6b5a52 50%,#3d3532 100%)" role="img" aria-label="Freunde stoßen bei einer Feier an"><span>Duis autem vel eum iriuren ok dolor in hendrerit.</span></div>
<div class="ev-small" style="left:566px;top:2718px;background:linear-gradient(180deg,#c9a27a 0%,#d98840 40%,#6a4a38 100%)" role="img" aria-label="Festivalzelte mit Heißluftballon"><span>Duis autem vel eum iriuren ok dolor in hendrerit.</span></div>
<div class="ev-small" style="left:823px;top:2718px;background:linear-gradient(180deg,#2a2a4a 0%,#8a4a3a 40%,#3a2a2a 100%)" role="img" aria-label="Nachtmarkt mit Lichterketten"><span>Duis autem vel eum iriuren ok dolor in hendrerit.</span></div>
<a class="btn abs" style="left:546px;top:2937px;width:106px;height:33px;font-size:12px">Alle anzeigen</a>

<!-- Anfahrt -->
<svg class="orn" style="top:3103px" viewBox="0 0 96 30"><line x1="0" y1="15" x2="34" y2="15" stroke="#7ab51d" stroke-width="1.5"/><line x1="62" y1="15" x2="96" y2="15" stroke="#1d6fb8" stroke-width="1.5"/><circle cx="48" cy="15" r="12" fill="#1d6fb8"/></svg>
<h2 class="sec-title" style="top:3140px"><span class="b">So erreichen</span> Sie uns</h2>
<div class="map" role="img" aria-label="Straßenkarte der Region mit Markierungen der Gastgeber"></div>

<svg class="footer-shape" width="1200" height="470" viewBox="0 0 1200 470">
  <path d="M0 132 Q520 -10 1200 110 L1200 470 L0 470Z" fill="#0b0b0b"/>
  <path d="M0 110 Q520 -10 1200 110 L1200 118 Q520 8 0 132Z" fill="#7ab51d"/>
</svg>

<footer class="footer">
  <div class="f-brand">
    <div class="dot"></div>
    <div class="brand-name">WANDERHOF KELBACH</div>
  </div>
  <div class="hours">
    <h4>Öffnungszeiten</h4>
    Mo-Do 9:00 - 16:00 Uhr<br>Fr 9:00 - 12:30 Uhr
  </div>
  <div class="vline" style="left:379px"></div>
  <div class="f-head" style="left:424px">Schnelle Links</div>
  <ul class="f-links" style="left:424px">
    <li class="active">» Startseite</li><li>» Kelbachtal</li><li>» Gastgeber</li><li>» Freizeit</li><li>» Ausflugsziele</li><li>» Kunst und Kultur</li>
  </ul>
  <ul class="f-links" style="left:624px">
    <li>» Information material</li><li>» imprint</li><li>» Data protection</li><li>» Veranstaltungen</li><li>» Kontakt</li>
  </ul>
  <div class="vline" style="left:800px"></div>
  <div class="f-head" style="left:845px">Kontakt Details</div>
  <div class="contact">
    <div class="row"><svg viewBox="0 0 30 30" fill="none" stroke="#fff" stroke-width="1.6"><path d="M15 27s-8-8-8-14a8 8 0 0 1 16 0c0 6-8 14-8 14z"/><circle cx="15" cy="13" r="3"/></svg><div>Marktplatz 3<br>12345 Kelbach</div></div>
    <div class="row"><svg viewBox="0 0 30 30" fill="none" stroke="#fff" stroke-width="1.6"><path d="M7 4h5l2 6-3 2a13 13 0 0 0 7 7l2-3 6 2v5a2 2 0 0 1-2 2A21 21 0 0 1 5 6a2 2 0 0 1 2-2z"/></svg><div>Telefon<br>01234 / 567 890</div></div>
    <div class="row"><svg viewBox="0 0 30 30" fill="none" stroke="#fff" stroke-width="1.6"><rect x="4" y="11" width="22" height="14"/><rect x="9" y="3" width="12" height="8"/><path d="M9 16h12M9 20h12"/></svg><div>Telefax<br>01234 / 567 899</div></div>
    <div class="row"><svg viewBox="0 0 30 30" fill="none" stroke="#fff" stroke-width="1.6"><rect x="3" y="8" width="24" height="16"/><path d="M3 8l12 9 12-9"/></svg><div>E-mail<br>info@wanderhof-kelbach.de</div></div>
  </div>
</footer>
<div class="copy">© 2025 WANDERHOF KELBACH. All Rights Reserved.</div>

</body>
</html>
```